Natural Medicine & Health/Fitness Coaching studio requires web page

Require a innovative web page for a studio that coaches clients to better health, nutrition and fitness. The studio compromises of Clinical Nutritionists, Naturopaths, Rehab Trainers, Personal Trainers and Sport Coaches. Would like to see earthy but bold designs emphasizing nutritional health and athletic performance.
Updates

Design only launched today.

Target Market(s)

All genders from 20's to 60's, as well as families

Industry/Entity Type

Nutritionist

Coding

Coded - Design and coding required

Number of Pages Required

3 page

Colors
abd037
3277b5
fbee3d
fece3e
33b8a4
f04a50

Requirements
Must have
• Online booking system, ability to message
• Home page
• Coaching/Fitness page
• Nutritional Medicine page
• Must be suitable for both Fitness and Nutrition

```html
<!DOCTYPE html>
<html lang="en">
<head>
<meta charset="utf-8">
<title>Rootwell Nutritional Therapy</title>
<link href="https://fonts.googleapis.com/css2?family=Poppins:wght@400;500;600;700&display=swap" rel="stylesheet">
<style>
:root{
  --navy:#1c4466;
  --heading:#1f5c8a;
  --green:#7dc242;
  --green-soft:#abd037;
  --blue:#3277b5;
  --teal:#33b8a4;
  --ink:#222;
  --dark:#141414;
  --white:#fff;
  --btn:linear-gradient(180deg,#8dc63f 0%,#3a86b0 100%);
}
*{box-sizing:border-box;margin:0;padding:0}
html,body{width:1200px;height:4557px;overflow:hidden;background:var(--white)}
body{position:relative;font-family:'Poppins',sans-serif;color:var(--ink)}
.abs{position:absolute}
.topbar{left:0;top:0;width:1200px;height:67px;background:var(--navy);color:#fff;font-size:15px}
.topbar .item{position:absolute;top:22px;display:flex;align-items:center;gap:12px}
.socials{display:flex;gap:12px}
.socials span{width:22px;height:22px;border-radius:4px;background:#fff;display:block}
.header{left:0;top:67px;width:1200px;height:152px;background:#fff}
.brand{position:absolute;left:91px;top:40px;display:flex;align-items:center;gap:14px}
.brand .dot{width:22px;height:22px;border-radius:50%;background:var(--green)}
.brand .name{font-size:42px;font-weight:600;color:var(--green);line-height:1}
.brand .sub{font-size:15px;color:var(--green);font-weight:500;margin-top:4px}
.nav{position:absolute;right:90px;top:66px;display:flex;gap:30px;font-size:16px}
.nav a{color:var(--ink);text-decoration:none}
.nav a.active{color:var(--blue);font-weight:600}
.hero{left:0;top:219px;width:1200px;height:640px;background:linear-gradient(110deg,#0e0e0e 0%,#262626 45%,#4a4036 70%,#1a1a1a 100%)}
.hero h1{position:absolute;left:91px;top:165px;color:#fff;font-size:54px;font-weight:600;line-height:1.2}
.hero p{position:absolute;left:91px;top:310px;color:#fff;font-size:16px;width:470px}
.btn{position:absolute;display:flex;align-items:center;justify-content:center;color:#fff;background:var(--btn);border-radius:5px;font-size:20px}
.hero-wave{left:0;top:640px;width:1200px;height:220px}
h2.section{position:absolute;width:1200px;left:0;text-align:center;font-size:38px;font-weight:600;color:var(--heading)}
.frame{background:var(--green)}
.photo{border:0}
.copy{font-size:16px;line-height:27px;color:var(--ink)}
.studio{left:0;top:1449px;width:1200px;height:465px;background:linear-gradient(180deg,var(--green) 0%,#58a48a 45%,var(--blue) 100%)}
.studio h2{position:absolute;width:1200px;top:36px;text-align:center;color:#fff;font-size:38px;font-weight:600}
.card{position:absolute;top:119px;width:234px;color:#fff}
.card .pic{width:234px;height:173px;border:5px solid #fff}
.card h3{font-size:22px;font-weight:600;margin-top:28px}
.card p{font-size:15px;line-height:21px;margin-top:10px}
.card .more{font-size:15px;margin-top:8px}
.arrow{position:absolute;width:40px;height:40px;border-radius:50%;display:flex;align-items:center;justify-content:center}
.booking{left:0;top:3020px;width:1200px;height:534px;background:linear-gradient(100deg,#1b1b1b 0%,#2c2a27 50%,#171717 100%)}
.booking h2{position:absolute;width:1200px;top:40px;text-align:center;color:#fff;font-size:38px;font-weight:600}
.field{position:absolute;background:#fff;height:40px;width:458px;font-size:13px;color:#444;padding:10px 8px}
.test-text{left:456px;top:3758px;width:610px;font-size:16px;line-height:27px}
.footer{left:0;top:4130px;width:1200px;height:427px;background:#000;color:#fff}
.footer h4{font-size:24px;font-weight:600;margin-bottom:14px}
.footer ul{list-style:none;font-size:16px;line-height:27px}
.fcol{position:absolute;top:80px}
</style>
</head>
<body>

<div class="abs topbar">
  <div class="item" style="left:91px">
    <svg width="16" height="22" viewBox="0 0 16 22"><path d="M8 0C3.6 0 0 3.5 0 7.8 0 13.7 8 22 8 22s8-8.3 8-14.2C16 3.5 12.4 0 8 0zm0 11a3.2 3.2 0 110-6.4A3.2 3.2 0 018 11z" fill="#fff"/></svg>
    <span>17 Cedar Grove Rd.&nbsp; Millbrook, NH 03100</span>
  </div>
  <div class="item" style="left:490px">
    <svg width="20" height="20" viewBox="0 0 24 24"><path d="M6.6 10.8a15.1 15.1 0 006.6 6.6l2.2-2.2c.3-.3.7-.4 1-.2 1.1.4 2.3.6 3.6.6.6 0 1 .4 1 1V20c0 .6-.4 1-1 1A17 17 0 013 4c0-.6.4-1 1-1h3.5c.6 0 1 .4 1 1 0 1.3.2 2.5.6 3.6.1.3 0 .7-.2 1z" fill="#fff"/></svg>
    <span>+61 400 123 456</span>
  </div>
  <div class="socials" style="position:absolute;right:92px;top:22px"><span></span><span></span><span></span><span></span><span></span></div>
</div>

<header class="abs header">
  <div class="brand">
    <span class="dot"></span>
    <div><div class="name">Rootwell</div><div class="sub">Nutritional Therapy</div></div>
  </div>
  <nav class="nav"><a class="active">Home</a><a>About us</a><a>Coaching</a><a>Fitness</a><a>Nutrition</a><a>Contact us</a></nav>
</header>

<section class="abs hero" role="img" aria-label="Athlete holding a shaker bottle in a dark gym">
  <h1>Rootwell<br>Nutritional Therapy</h1>
  <p>Lorem Ipsum is simply dummy text of the printing and typesetting industry.</p>
  <div class="btn" style="left:91px;top:395px;width:189px;height:50px">View More</div>
</section>
<svg class="abs hero-wave" viewBox="0 0 1200 220" preserveAspectRatio="none">
  <defs><linearGradient id="hw" x1="0" x2="1"><stop offset="0" stop-color="#7dc242"/><stop offset="1" stop-color="#3277b5"/></linearGradient></defs>
  <path d="M0 200 C300 120 600 40 900 60 C1050 70 1150 120 1200 150 L1200 220 L0 220Z" fill="url(#hw)"/>
  <path d="M0 220 C300 150 600 80 900 90 C1050 96 1150 140 1200 170 L1200 220Z" fill="#fff"/>
</svg>

<h2 class="section" style="top:910px">About us</h2>
<div class="abs frame" style="left:91px;top:1042px;width:441px;height:340px"></div>
<div class="abs photo" role="img" aria-label="Man resting with a juice glass in a gym" style="left:137px;top:1012px;width:446px;height:340px;background:linear-gradient(135deg,#c9ccd0,#6f7880 55%,#2d3d55)"></div>
<p class="abs copy" style="left:614px;top:1068px;width:470px">It is a long established fact that a reader will be distracted by the readable content of a page when looking at its layout. The point of using Lorem Ipsum is that it has a more-or-less normal distribution of letters, as opposed to using 'Content here, content here', making it look like readable English.</p>
<div class="btn" style="left:614px;top:1270px;width:188px;height:52px">Read More</div>

<section class="abs studio">
  <h2>Studio Compromises</h2>
  <div class="arrow" style="left:12px;top:211px;background:#fff"><svg width="14" height="14" viewBox="0 0 14 14"><path d="M9 2L4 7l5 5" stroke="#333" stroke-width="2.5" fill="none"/></svg></div>
  <div class="arrow" style="left:1132px;top:211px;background:#fff"><svg width="14" height="14" viewBox="0 0 14 14"><path d="M5 2l5 5-5 5" stroke="#333" stroke-width="2.5" fill="none"/></svg></div>
  <div class="card" style="left:85px"><div class="pic" role="img" aria-label="Nutritionist holding an apple" style="background:linear-gradient(135deg,#f2f2f2,#cfd8d2)"></div><h3>Clinical Nutritionists</h3><p>It is a long established fact that a reader.</p><div class="more">Read More &gt;&gt;</div></div>
  <div class="card" style="left:349px"><div class="pic" role="img" aria-label="Therapist giving a head massage" style="background:linear-gradient(135deg,#e8d6c8,#b98f74)"></div><h3>Naturopaths</h3><p>It is a long established fact that a reader.</p><div class="more">Read More &gt;&gt;</div></div>
  <div class="card" style="left:611px"><div class="pic" role="img" aria-label="Coloured exercise balls in a studio" style="background:linear-gradient(135deg,#c8302d,#7a1f2a 60%,#2f5e8a)"></div><h3>Sport Coaches</h3><p>It is a long established fact that a reader.</p><div class="more">Read More &gt;&gt;</div></div>
  <div class="card" style="left:878px"><div class="pic" role="img" aria-label="Trainer working out with a client" style="background:linear-gradient(135deg,#8a8a8a,#3b3b3b 60%,#b83b3b)"></div><h3>Personal Trainers</h3><p>It is a long established fact that a reader.</p><div class="more">Read More &gt;&gt;</div></div>
</section>

<h2 class="abs" style="left:91px;top:2020px;font-size:38px;font-weight:600;color:var(--heading)">Fitness</h2>
<p class="abs copy" style="left:91px;top:2095px;width:470px">It is a long established fact that a reader will be distracted by the readable content of a page when looking at its layout. The point of using Lorem Ipsum is that it has a more-or-less normal distribution of letters, as opposed to using 'Content here, content here', making it look like readable English.</p>
<div class="btn" style="left:91px;top:2293px;width:188px;height:55px">Read More</div>
<div class="abs frame" style="left:614px;top:2029px;width:449px;height:341px"></div>
<div class="abs photo" role="img" aria-label="Woman doing push-ups with dumbbells" style="left:662px;top:1999px;width:447px;height:340px;background:linear-gradient(135deg,#d08a4a,#5a3a26 50%,#1a2a3a)"></div>

<div class="abs frame" style="left:91px;top:2582px;width:444px;height:334px"></div>
<div class="abs photo" role="img" aria-label="Woman at a table with fresh vegetables" style="left:137px;top:2549px;width:446px;height:337px;background:linear-gradient(135deg,#f1ede4,#c9c2ac 50%,#6f8a4a)"></div>
<h2 class="abs" style="left:632px;top:2555px;font-size:38px;font-weight:600;color:var(--heading)">Nutrition</h2>
<p class="abs copy" style="left:632px;top:2625px;width:470px">It is a long established fact that a reader will be distracted by the readable content of a page when looking at its layout. The point of using Lorem Ipsum is that it has a more-or-less normal distribution of letters, as opposed to using 'Content here, content here', making it look like readable English.</p>
<div class="btn" style="left:632px;top:2828px;width:187px;height:55px">Read More</div>

<section class="abs booking" role="img" aria-label="Dim gym interior behind the booking form">
  <h2>Book Appointments</h2>
  <div class="field" style="left:128px;top:127px">Name</div>
  <div class="field" style="left:611px;top:127px">Email</div>
  <div class="field" style="left:128px;top:182px">Phone Number</div>
  <div class="field" style="left:611px;top:182px">Address</div>
  <div class="field" style="left:128px;top:237px">Service You need</div>
  <div class="field" style="left:611px;top:237px">Appointment Date &amp; Time</div>
  <div class="field" style="left:128px;top:288px;width:941px;height:116px">Messages</div>
  <div class="btn" style="left:492px;top:437px;width:185px;height:52px">Submit Now</div>
</section>

<h2 class="section" style="top:3633px">Testimonials</h2>
<div class="arrow" style="left:29px;top:3796px;background:var(--heading)"><svg width="14" height="14" viewBox="0 0 14 14"><path d="M9 2L4 7l5 5" stroke="#fff" stroke-width="2.5" fill="none"/></svg></div>
<div class="arrow" style="left:1131px;top:3796px;background:var(--heading)"><svg width="14" height="14" viewBox="0 0 14 14"><path d="M5 2l5 5-5 5" stroke="#fff" stroke-width="2.5" fill="none"/></svg></div>
<div class="abs" role="img" aria-label="Customer portrait" style="left:158px;top:3710px;width:212px;height:212px;border-radius:50%;background:linear-gradient(160deg,#cbd3dc,#7d8c9a 60%,#d9b23a)"></div>
<div class="abs" style="left:337px;top:3788px;width:56px;height:56px;border-radius:50%;background:var(--heading);color:#fff;font-size:40px;font-weight:700;text-align:center;line-height:70px">&#8221;</div>
<div class="abs" style="left:431px;top:3722px;width:2px;height:213px;background:#ccc"></div>
<div class="abs test-text">It is a long established fact that a reader will be distracted by the readable content of a page when looking at its layout.<br>The point of using Lorem Ipsum is that it has a more-or-less normal distribution of letters<p style="margin-top:12px;font-weight:600;font-size:15px">- Jordan , Customer</p></div>

<svg class="abs" style="left:0;top:3990px" width="1200" height="150" viewBox="0 0 1200 150" preserveAspectRatio="none">
  <defs><linearGradient id="fw" x1="0" x2="1"><stop offset="0" stop-color="#7dc242"/><stop offset="1" stop-color="#3277b5"/></linearGradient></defs>
  <path d="M0 30 C250 110 500 140 800 90 C1000 55 1120 40 1200 50 L1200 150 L0 150Z" fill="url(#fw)"/>
  <path d="M0 60 C250 140 500 160 800 115 C1000 85 1120 70 1200 80 L1200 150 L0 150Z" fill="#000"/>
</svg>
<footer class="abs footer">
  <div class="abs" style="left:91px;top:170px;display:flex;align-items:center;gap:12px">
    <span style="width:20px;height:20px;border-radius:50%;background:#fff;display:block"></span>
    <div><div style="font-size:40px;font-weight:600;line-height:1">Rootwell</div><div style="font-size:14px;margin-top:4px">Nutritional Therapy</div></div>
  </div>
  <div class="fcol" style="left:404px"><h4>Quick Links</h4><ul><li>Home</li><li>About Us</li><li>Coaching</li><li>Fitness</li><li>Nutrition</li><li>Contact Us</li></ul></div>
  <div class="fcol" style="left:605px"><h4>Studio Compromises</h4><ul><li>Clinical Nutritionists</li><li>Naturopaths</li><li>Rehab Trainers</li><li>Personal Trainers</li><li>Sport Coaches</li></ul></div>
  <div class="fcol" style="left:887px"><h4>NewsLetter</h4><p style="font-size:15px;line-height:21px;width:200px">Email newsletters are a Rootwell</p>
    <div style="margin-top:20px;width:228px;height:30px;background:#fff;color:#444;font-size:12px;padding:7px 8px">Enter the email</div>
    <div style="margin:25px 0 0 52px;width:100px;height:25px;background:var(--btn);border-radius:3px;font-size:14px;text-align:center;line-height:25px">Send</div>
  </div>
  <div class="abs" style="left:91px;top:364px;font-size:14px">&copy; 2019 Rootwell. All Rights Reserved</div>
  <div class="socials abs" style="left:940px;top:362px"><span></span><span></span><span></span><span></span><span></span></div>
</footer>

</body>
</html>
```